We need letterhead, Business Cards, and envelops designed. We have attached a design of our logo and a sample of letterhead idea that was started but never perfected, it is only an idea for the letterhead if you can design something better we may love that also we are open to change.
We want a design that looks professional in style. we are a non profit trade association in the construction industry. the green color in the attached design represent green building, and we like that. also if you just want to enhance the letterhead sample that we attached that would be fine also.
Thanks and good luck
also the name that should show on the first business cards should be Morgan Feltwick, Director are web address is www.pvtrn.org

```html
<!DOCTYPE html>
<html lang="en">
<head>
<meta charset="utf-8">
<title>PVTRN Letterhead</title>
<link href="https://fonts.googleapis.com/css2?family=Questrial&display=swap" rel="stylesheet">
<style>
  :root {
    --ink: #111111;
    --text: #3a3a3a;
    --green: #3d8a22;
    --green-faint: #dbe5d5;
    --band: #000000;
    --paper: #ffffff;
  }
  html, body {
    margin: 0;
    padding: 0;
    overflow: hidden;
    background: var(--paper);
  }
  .letterhead {
    position: relative;
    width: 927px;
    height: 1200px;
    overflow: hidden;
    background: var(--paper);
    font-family: "Questrial", "Century Gothic", sans-serif;
  }
  .brand {
    position: absolute;
    left: 90px;
    top: 76px;
    display: flex;
    align-items: center;
    gap: 14px;
  }
  .brand-mark {
    width: 34px;
    height: 34px;
    background: var(--green);
  }
  .brand-name {
    font-size: 62px;
    line-height: 1;
    letter-spacing: 4px;
    color: var(--ink);
  }
  .contact {
    position: absolute;
    right: 94px;
    top: 75px;
    text-align: right;
    font-size: 13px;
    line-height: 17.5px;
    letter-spacing: 2px;
    color: var(--text);
  }
  .contact p { margin: 0; }
  .contact .phones { margin-top: 16px; margin-right: -22px; }
  .contact .line {
    display: flex;
    justify-content: flex-end;
    align-items: center;
    gap: 10px;
  }
  .contact svg { width: 12px; height: 12px; fill: var(--green); }
  .backdrop-block {
    position: absolute;
    left: 0;
    top: 832px;
    width: 300px;
    height: 300px;
    background: var(--green-faint);
  }
  .footer-band {
    position: absolute;
    left: 0;
    bottom: 0;
    width: 927px;
    height: 60px;
    background: var(--band);
    display: flex;
    align-items: center;
    justify-content: center;
  }
  .footer-band .web {
    color: #ffffff;
    font-size: 17px;
    letter-spacing: 3.5px;
  }
</style>
</head>
<body>
<main class="letterhead">
  <header class="brand">
    <span class="brand-name">PVTRN</span>
    <span class="brand-mark"></span>
  </header>

  <address class="contact">
    <p>address</p>
    <p>4321 first street</p>
    <p>anytown, State ZIP</p>
    <div class="phones">
      <p class="line">123-456-7890
        <svg viewBox="0 0 12 12" aria-label="phone"><path d="M1 3 Q6 0 11 3 L10 5 L8 4.5 L8 3.5 Q6 3 4 3.5 L4 4.5 L2 5 Z M3 6 H9 L10 11 H2 Z"/></svg>
      </p>
      <p class="line">123-456-7891
        <svg viewBox="0 0 12 12" aria-label="fax"><path d="M3 1 H9 V4 H3 Z M1 5 H11 V9 H9 V11 H3 V9 H1 Z M4 8 V10 H8 V8 Z" fill-rule="evenodd"/></svg>
      </p>
    </div>
  </address>

  <div class="backdrop-block" aria-hidden="true"></div>

  <footer class="footer-band">
    <span class="web">www.pvtrn.org</span>
  </footer>
</main>
</body>
</html>
```